Modern, clean and professional Wordpress design for a safety training company!

We are currently in the process of creating a new website for our business. We have hired a website developer and the main structure of our new Wordpress site is complete. We now need an overall design plan for the site. We need a very clean, professional and easy to follow website. Most of our website visitors only spend about 30-45 secs on our sites "shopping " so it is imperative that we have a strong Home Page.
Our company specializes in CPR and First Aid Certification Classes to businesses and individuals throughout Northern California. We provide these certifications two ways: ONSITE-We come to you, and HOSTED-we offer weekly classes at our 2 locations.
Our design needs to use the general green and blue colors of our logo. But we also like white.
The final design MUST communicate a legitimate, trustworthy and professional business. Our industry is VERY competitive and we need to STAND OUT.
Currently, the NEW website that we need a new design for is www.LifelineDrillWorks.com
Our old website is www.RescuePrepValleyHub.com and we really do like the design of this website, but we just needed a Wordpress site for SEO purposes.
These are 3 websites that we really:
http://morvaliontech.com/
http://www.tralbex.com/
https://www.plivant.com/
I have attached our Logo and other images if you need to use them but looking at the current two sites will be you best help.
Target Market(s)
1) Large businesses and industries that are looking for a company to provide ONSITE safety training classes at their office or place of work.
2) Individuals that need certifications for their jobs and other needs. These individuals are looking for a legitimate, trustworthy and professional environment to complete their training class.

```html
<!DOCTYPE html>
<html lang="en">
<head>
<meta charset="utf-8">
<title>Valley Rescue Academy – CPR &amp; First Aid Classes</title>
<link rel="stylesheet" href="https://fonts.googleapis.com/css2?family=Fira+Sans:wght@400;500&family=Open+Sans:wght@400;600&family=Raleway:wght@400;500&display=swap">
<style>
:root{
  --green:#8cc63f;
  --green-dark:#6aa626;
  --blue:#233a8f;
  --navy-text:#2a3f9a;
  --nav-bg:#464646;
  --footer-bg:#2b2b2b;
  --text:#444;
  --muted:#666;
  --card-grey:#f0f0f0;
  --white:#fff;
}
*{box-sizing:border-box;margin:0;padding:0}
html,body{width:774px;height:1200px;overflow:hidden;background:var(--white)}
body{position:relative;font-family:"Open Sans",sans-serif;color:var(--text)}
.abs{position:absolute}

/* header */
.brand{left:84px;top:30px;display:flex;align-items:center;gap:8px}
.brand-mark{width:16px;height:16px;border-radius:50%;background:var(--green)}
.brand-name{font-family:"Raleway",sans-serif;font-weight:500;font-size:17px;color:var(--blue);line-height:1.15;width:120px}
.contact-top{right:86px;top:31px;font-size:9px;color:#555;line-height:18px}
.contact-top div{display:flex;align-items:center;gap:6px}
.contact-top .phone-num{font-size:11px}
.contact-top svg{width:9px;height:9px}

/* nav */
.main-nav{left:0;top:88px;width:774px;height:34px;background:var(--nav-bg);border-bottom:2px solid var(--green)}
.main-nav a{position:absolute;top:0;height:32px;line-height:32px;font-size:8.4px;color:var(--white);text-decoration:none;text-transform:uppercase;letter-spacing:.2px;font-weight:600}
.main-nav a.active{background:var(--green);left:84px;width:77px;text-align:center}

/* hero */
.hero{left:0;top:122px;width:774px;height:308px;background:linear-gradient(180deg,#d8d6d0 0%,#b9aea0 40%,#6d5a4c 75%,#3e3631 100%)}
.hero-arrow{width:26px;height:26px;border-radius:50%;background:var(--white);top:262px;display:flex;align-items:center;justify-content:center;box-shadow:0 1px 3px rgba(0,0,0,.3)}
.hero-caption{left:213px;top:353px;width:348px;height:60px;background:rgba(30,30,30,.82);font-family:"Fira Sans",sans-serif}
.hero-caption h2{position:absolute;left:16px;top:8px;font-weight:400;font-size:22px;color:var(--green)}
.hero-caption p{position:absolute;left:16px;top:36px;font-size:11px;color:var(--white)}
.btn-blue{display:block;background:var(--blue);color:var(--white);font-family:"Fira Sans",sans-serif;font-size:9.5px;text-align:center;text-decoration:none}
.hero-caption .btn-blue{position:absolute;left:232px;top:17px;width:100px;height:25px;line-height:25px}

/* welcome */
.welcome{left:0;top:460px;width:774px;text-align:center}
.welcome h1{font-family:"Raleway",sans-serif;font-weight:400;font-size:20.5px;color:#333}
.welcome .rule{width:70px;height:1px;background:var(--green);margin:9px auto 0}
.welcome p{width:600px;margin:14px auto 0;font-size:7.6px;line-height:15.5px;color:var(--muted)}
.btn-green{display:inline-block;margin-top:11px;width:79px;height:23px;line-height:23px;background:var(--green);color:var(--white);font-family:"Fira Sans",sans-serif;font-size:9px;text-decoration:none}

/* pricing band */
.price-band{left:0;top:614px;width:774px;height:242px;background:linear-gradient(110deg,#5d6878 0%,#8a7766 35%,#b08c73 55%,#566171 80%,#3c4550 100%)}
.price-card{top:655px;width:285px;height:163px;background:var(--white);padding:8px}
.price-card .inner{border:1px solid #ddd;height:100%;text-align:center;padding-top:20px}
.price-card h3{font-family:"Raleway",sans-serif;font-weight:400;font-size:20px;color:var(--navy-text)}
.price-card .price{font-family:"Fira Sans",sans-serif;font-weight:500;font-size:28px;color:var(--green-dark);margin-top:2px}
.price-card .desc{font-family:"Raleway",sans-serif;font-size:11px;color:#333;margin-top:3px}
.price-card .btn-blue{width:96px;height:24px;line-height:24px;margin:13px auto 0}

/* reviews */
.reviews-title{left:0;top:890px;width:774px;text-align:center;font-family:"Raleway",sans-serif;font-size:18.5px;color:#333;letter-spacing:.5px}
.review{top:929px;width:194px;height:89px;background:var(--card-grey);text-align:center;font-size:7.8px;color:#444;padding-top:13px;line-height:16.3px}
.review .stars{color:#f5a623;font-size:10px;letter-spacing:1px}
.review .stars .off{color:#bbb}
.dots{left:377px;top:1033px;display:flex;gap:5px}
.dots span{width:7px;height:7px;border-radius:50%;background:#ddd}
.dots span.on{background:var(--green)}

/* footer */
.site-footer{left:0;top:1079px;width:774px;height:121px;background:var(--footer-bg)}
.footer-label{font-size:8.5px;color:#ddd;text-transform:uppercase;letter-spacing:.2px}
.social{left:86px;top:1131px;display:flex;gap:5px}
.social span{width:19px;height:19px;border-radius:50%;background:var(--white)}
.copyright{left:85px;top:1176px;font-size:8px;color:#aaa}
.map{left:313px;top:1098px;width:169px;height:84px;background:linear-gradient(135deg,#e6e2d8,#cfd9c4 50%,#e4d6b8)}
.contact-lines{left:498px;top:1128px;font-size:8px;color:#bbb;line-height:16.2px}
</style>
</head>
<body>

<header>
  <div class="abs brand">
    <span class="brand-mark"></span>
    <span class="brand-name">Valley Rescue Academy</span>
  </div>
  <div class="abs contact-top">
    <div><svg viewBox="0 0 10 10"><rect width="10" height="10" rx="1.5" fill="#8cc63f"/><path d="M3 2.3l1 1.6-.6.7a4 4 0 0 0 2 2l.7-.6 1.6 1-.5 1.1C4.8 8 2 5.3 2 2.8z" fill="#fff"/></svg>Call Us <span class="phone-num">916-555-0187</span></div>
    <div><svg viewBox="0 0 10 10"><rect y="1.5" width="10" height="7" rx="1" fill="#8cc63f"/><path d="M.5 2.2L5 5.6l4.5-3.4" stroke="#fff" stroke-width="1" fill="none"/></svg>Email: info@valleyrescueacademy.com</div>
  </div>
</header>

<nav class="abs main-nav">
  <a class="active" href="#">Home</a>
  <a href="#" style="left:186px">Class Calender</a>
  <a href="#" style="left:294px">Classes for Groups</a>
  <a href="#" style="left:417px">Certification Classes</a>
  <a href="#" style="left:553px">About Us</a>
  <a href="#" style="left:636px">Policies</a>
</nav>

<section>
  <div class="abs hero" role="img" aria-label="Photo of a seated audience attending a training class with an instructor presenting at the front"></div>
  <div class="abs hero-arrow" style="left:75px"><svg width="10" height="10" viewBox="0 0 10 10"><path d="M7 1L3 5l4 4" stroke="#333" stroke-width="2" fill="none"/></svg></div>
  <div class="abs hero-arrow" style="left:673px"><svg width="10" height="10" viewBox="0 0 10 10"><path d="M3 1l4 4-4 4" stroke="#333" stroke-width="2" fill="none"/></svg></div>
  <div class="abs hero-caption">
    <h2>CPR+First Aid</h2>
    <p>$59 Adult/Child/Infant 3 hours or less!</p>
    <a class="btn-blue" href="#">Register Now</a>
  </div>
</section>

<section class="abs welcome">
  <h1>Welcome to Valley Rescue Academy!</h1>
  <div class="rule"></div>
  <p>Valley Rescue Academy is Northern California's leader in CPR, BLS, and Basic First Aid Certifications! Taught by experienced Firefighters, our classes are much shorter and provide common sense knowledge and skills to each student to help prepare them for actual emergencies. By using real life emergency responders, we have revolutionized the standard, boring CPR class by teaching students.</p>
  <a class="btn-green" href="#">Read More</a>
</section>

<section>
  <div class="abs price-band" role="img" aria-label="Blurred photo of hands practising CPR compressions on a training manikin"></div>
  <div class="abs price-card" style="left:86px"><div class="inner">
    <h3>CPR</h3>
    <div class="price">$39.00</div>
    <div class="desc">Adult/Child/Infant&nbsp; 90 Minutes!</div>
    <a class="btn-blue" href="#">Register Now</a>
  </div></div>
  <div class="abs price-card" style="left:403px"><div class="inner">
    <h3>BLS</h3>
    <div class="price">$49.00</div>
    <div class="desc">Healthcare/Dental&nbsp; 90 Minutes!</div>
    <a class="btn-blue" href="#">Register Now</a>
  </div></div>
</section>

<section>
  <h2 class="abs reviews-title">REVIEWS</h2>
  <div class="abs review" style="left:84px">
    <div class="stars">★★★★<span class="off">☆</span></div>
    <div>Dana- CA, United States</div>
    <div>March 15, 2014</div>
    <div>Most fun CPR class, most easy to...</div>
  </div>
  <div class="abs review" style="left:290px">
    <div class="stars">★★★★<span class="off">☆</span></div>
    <div>Marcus T- CA, United States</div>
    <div>February 26, 2014</div>
    <div>I enjoyed the CPR class it was...</div>
  </div>
  <div class="abs review" style="left:497px">
    <div class="stars">★★★★<span class="off">☆</span></div>
    <div>Ellen- CA, United States</div>
    <div>February 26, 2014</div>
    <div>The instructor was awesome! Spoke...</div>
  </div>
  <div class="abs dots"><span class="on"></span><span></span></div>
</section>

<footer>
  <div class="abs site-footer"></div>
  <div class="abs footer-label" style="left:86px;top:1107px">Follow Us</div>
  <div class="abs social">
    <span aria-label="Social link"></span><span aria-label="Social link"></span><span aria-label="Social link"></span><span aria-label="Social link"></span><span aria-label="Feed link"></span>
  </div>
  <div class="abs copyright">©2015. Yoursite All Right Reserved.</div>
  <div class="abs map" role="img" aria-label="Street map showing the training centre location"></div>
  <div class="abs footer-label" style="left:497px;top:1107px;font-weight:600">Contact Us</div>
  <div class="abs contact-lines">
    <div>The Company Name Inc.</div>
    <div>412 Harbor Lane, Suite 8, Fairmont, CA 95610.</div>
    <div>Telephone: +1 800 555 0142</div>
  </div>
</footer>

</body>
</html>
```